CD Cover für junge Pop-Rock Band
Sehr kreative vorschläge. mehrere designs, die alle unter den top-favoriten für uns waren. änderungen und anpassungen stets schnell umgesetzt und auch nach gewinner-auswahl noch weiter zusammen gearbeitet bevor das endgültige design übergeben wurde.
Zielgruppe
Wir sind eine junge Band aus München und machen ausschließlich eigene Songs im Bereich Pop-Rock. Durch Einflüsse aus verschiedenen anderen Genres wie Funk, Reggae und Britpop grenzen sich unsere Songs von typischem Mainstream-Pop ab. Unsere Zielgruppe setzt sich aus Personen verschiedener Altersgruppen zusammen, der Fokus liegt jedoch auf Mitte Zwanzig- bis Mitte Dreißig-Jährigen.
Homepage: www.okapimind.com
Sozialnetz: www.sozialnetz.example/okapimindband
Aufgabenstellung
Wir benötigen ein Design für unsere neue EP "Open Gates". Diese wird in Form eines DigiPacks veröffentlicht werden. Daher werden Designs für Vorderseite, Rückseite, zwei Innenseiten sowie die CD selbst benötigt.
Folgendes sollte auf den jeweiligen Seiten enthalten sein:
Vorderseite:
- Bandschriftzug (siehe Anhang)
- Name der EP: Open Gates
Rückseite:
- Trackliste (1.Velvet Spoon, 2.Hold It Near, 3.Harbor Pike, 4.Can We Stay, 5.Brightest Edge)
- Credits (Recording by ..., Mix by ..., Mastering by ..., etc. -> wird noch festgesetzt)
Anmerkung:
Die roten Kratzer aus dem Bandlogo können bei Bedarf frei verwendet werden hinsichtlich Farbe, Muster, Gestaltung, Größe, etc.
Wir möchten keine Bilder von uns (z.B. von unserer Homepage, Sozialnetz, etc) auf der CD.

```html
<!DOCTYPE html>
<html lang="en">
<head>
<meta charset="utf-8">
<title>Okapimind – Open Gates disc label</title>
<link rel="stylesheet" href="https://fonts.googleapis.com/css2?family=Open+Sans:wght@300;400&display=swap">
<style>
  :root {
    --page: #ffffff;
    --ink-light: #ffffff;
    --tone-light: #d9d9d9;
    --tone-mid: #7a7a7a;
    --tone-dark: #1e1e1e;
    --hole: #ffffff;
  }
  html, body {
    margin: 0;
    padding: 0;
    width: 1200px;
    height: 1200px;
    overflow: hidden;
    background: var(--page);
  }
  .canvas {
    position: relative;
    width: 1200px;
    height: 1200px;
    font-family: "Open Sans", sans-serif;
    color: var(--ink-light);
  }
  .disc {
    position: absolute;
    left: 0;
    top: 0;
    width: 1200px;
    height: 1200px;
    border-radius: 50%;
    overflow: hidden;
  }
  .disc-photo {
    position: absolute;
    inset: 0;
    background:
      radial-gradient(ellipse 60% 30% at 50% 3%, var(--tone-light), transparent 70%),
      radial-gradient(ellipse 40% 35% at 20% 80%, var(--tone-dark), transparent 75%),
      radial-gradient(ellipse 45% 40% at 75% 40%, #3a3a3a, transparent 80%),
      linear-gradient(180deg, #5c5c5c 0%, var(--tone-mid) 55%, #9a9a9a 100%);
  }
  .disc-hole {
    position: absolute;
    left: 499px;
    top: 499px;
    width: 202px;
    height: 202px;
    border-radius: 50%;
    background: var(--hole);
  }
  .band-name {
    position: absolute;
    left: 0;
    right: 0;
    top: 248px;
    text-align: center;
    font-weight: 300;
    font-size: 100px;
    letter-spacing: 2px;
    line-height: 1;
    color: var(--ink-light);
  }
  .ep-title {
    position: absolute;
    top: 556px;
    font-weight: 400;
    font-size: 92px;
    line-height: 1;
    letter-spacing: -1px;
  }
  .ep-title--left { left: 58px; }
  .ep-title--right { right: 86px; }
  .tracklist {
    position: absolute;
    left: 0;
    right: 0;
    top: 810px;
    margin: 0;
    padding: 0;
    list-style: none;
    text-align: center;
    font-size: 38px;
    font-weight: 400;
    line-height: 65px;
    text-shadow: 0 0 14px rgba(0,0,0,0.55);
  }
</style>
</head>
<body>
<main class="canvas">
  <section class="disc">
    <div class="disc-photo" role="img" aria-label="Black and white photograph of two zebras, one with its mouth wide open, filling the disc"></div>
    <div class="disc-hole"></div>
    <div class="band-name">OKAPIMIND</div>
    <div class="ep-title ep-title--left">OPEN</div>
    <div class="ep-title ep-title--right">GATES</div>
    <ol class="tracklist">
      <li>1. Velvet Spoon</li>
      <li>2. Hold It Near</li>
      <li>3. Harbor Pike</li>
      <li>4. Can We Stay</li>
      <li>5. Brightest Edge</li>
    </ol>
  </section>
</main>
</body>
</html>
```